Oil Field Service company needs professional business cards

Looking to clean up our current company business cards and look a little more professional. Brenwick Casing Services is a US based company that services the oil field. We deal with engineers, managers and oil rigs....................................................................................................................................................................................................................................................................................................................................................................................................

Target Market(s)

Oil and Gas professionals

Industry/Entity Type

Oil And Gas

Contact Information for Business Card

See attached photo as example

Font styles to use
Sans Serif

Colors
ec1f27

Requirements
Must have
• Company Logo, Name, Title, Cell, Office, Fax, Email.
• See attached photo
Nice to have
• External CRT, Internal CRT, Casing Crews, Torque Turn, Laydown Machine
Should not have
• Do not introduce any new pictures and keep it professional looking

```html
<!DOCTYPE html>
<html lang="en">
<head>
<meta charset="utf-8">
<title>Brenwick Casing Services – Business Card</title>
<link rel="stylesheet" href="https://fonts.googleapis.com/css2?family=Questrial&display=swap">
<style>
  :root {
    --brand-red: #ec1f27;
    --band-red: #c8202a;
    --slate: #48525c;
    --ink: #3b434b;
    --card-bg: #f4f4f4;
    --page-bg: #9a9a9a;
    --white: #ffffff;
  }
  html, body {
    margin: 0;
    padding: 0;
    width: 1200px;
    height: 965px;
    overflow: hidden;
    background: var(--page-bg);
    font-family: "Questrial", sans-serif;
  }
  .card {
    position: absolute;
    left: 75px;
    top: 182px;
    width: 1050px;
    height: 600px;
    background: radial-gradient(ellipse at 45% 40%, var(--white) 0%, var(--card-bg) 60%, #e6e6e6 100%);
    overflow: hidden;
  }
  .brand {
    position: absolute;
    left: 60px;
    top: 205px;
    width: 460px;
    text-align: center;
    color: var(--slate);
  }
  .brand-name {
    font-size: 64px;
    line-height: 1;
    letter-spacing: 2px;
    text-transform: uppercase;
  }
  .brand-tagline {
    margin-top: 16px;
    font-size: 24px;
    letter-spacing: 5px;
    text-transform: uppercase;
  }
  .divider {
    position: absolute;
    left: 577px;
    top: 125px;
    width: 2px;
    height: 292px;
    background: linear-gradient(to bottom, transparent, var(--slate) 15%, var(--slate) 85%, transparent);
  }
  .contact {
    position: absolute;
    left: 629px;
    top: 138px;
    color: var(--ink);
  }
  .person-name {
    margin: 0;
    font-size: 34px;
    font-weight: 400;
    color: var(--brand-red);
    line-height: 1.1;
  }
  .person-title {
    margin: 0 0 28px;
    font-size: 25px;
    line-height: 1.2;
  }
  .contact-list {
    list-style: none;
    margin: 0;
    padding: 0;
  }
  .contact-list li {
    display: flex;
    align-items: center;
    font-size: 24px;
    line-height: 30px;
  }
  .contact-list svg {
    width: 24px;
    height: 22px;
    margin-right: 14px;
    fill: var(--brand-red);
    flex: none;
  }
  .address {
    margin: 22px 0 0;
    font-size: 24px;
  }
  .rule {
    position: absolute;
    left: 0;
    top: 543px;
    width: 100%;
    height: 6px;
    background: var(--slate);
  }
  .services {
    position: absolute;
    left: 0;
    top: 549px;
    width: 100%;
    height: 51px;
    background: var(--band-red);
    color: var(--white);
    font-size: 24px;
    line-height: 51px;
    text-align: center;
  }
</style>
</head>
<body>
  <div class="card">
    <div class="brand">
      <div class="brand-name">Brenwick</div>
      <div class="brand-tagline">Casing Services</div>
    </div>

    <div class="divider"></div>

    <div class="contact">
      <h1 class="person-name">Wade Hollister</h1>
      <p class="person-title">Area Manager</p>
      <ul class="contact-list">
        <li>
          <svg viewBox="0 0 24 22" aria-label="Office"><rect x="2" y="1" width="6" height="20" rx="1"/><rect x="9" y="3" width="13" height="18" rx="1"/><rect x="11" y="5" width="9" height="4" fill="#fff"/><rect x="11" y="11" width="2" height="2" fill="#fff"/><rect x="15" y="11" width="2" height="2" fill="#fff"/><rect x="11" y="15" width="2" height="2" fill="#fff"/><rect x="15" y="15" width="2" height="2" fill="#fff"/></svg>
          (555) 410 2870
        </li>
        <li>
          <svg viewBox="0 0 24 22" aria-label="Cell"><rect x="6" y="0" width="12" height="22" rx="2"/><rect x="8" y="3" width="8" height="13" fill="#fff"/><circle cx="12" cy="19" r="1.3" fill="#fff"/></svg>
          (555) 618 3042
        </li>
        <li>
          <svg viewBox="0 0 24 22" aria-label="Fax"><rect x="6" y="0" width="12" height="7" fill="none" stroke="#ec1f27" stroke-width="2"/><rect x="1" y="7" width="22" height="11" rx="2"/><rect x="5" y="15" width="14" height="7"/><rect x="7" y="17" width="10" height="1.5" fill="#fff"/></svg>
          (555) 410 2875
        </li>
        <li>
          <svg viewBox="0 0 24 22" aria-label="Email"><rect x="1" y="4" width="22" height="15"/><path d="M1 4 L12 13 L23 4" fill="none" stroke="#fff" stroke-width="2"/><path d="M1 19 L9 11 M23 19 L15 11" stroke="#fff" stroke-width="1.5"/></svg>
          whollister@brenwickcs.com
        </li>
      </ul>
      <p class="address">Alder Creek, OK 73990</p>
    </div>

    <div class="rule"></div>
    <div class="services">External CRT, Internal CRT, Casing Crews, Torque Turn, Laydown Machine</div>
  </div>
</body>
</html>
```